Ridgeline Journeys business card

please see website
www.ridgelinejourneys.comau

info needed on card
Curtis Halvey
Ph
email
Adventure Riding GPS trails

please use my logo and colours off my site

Curtis Halvey
curtis@ridgelinejourneys.com

```html
<!DOCTYPE html>
<html lang="en">
<head>
<meta charset="utf-8">
<title>Ridgeline Journeys – Business Card</title>
<link rel="stylesheet" href="https://fonts.googleapis.com/css2?family=Source+Sans+3:ital,wght@0,400;0,600;1,700&display=swap">
<style>
  :root {
    --backdrop: #4a4a4a;
    --card-white: #f7f7f7;
    --card-black: #000000;
    --accent-yellow: #f5d800;
    --accent-amber: #f2b705;
    --ink: #161616;
    --text-light: #ffffff;
  }
  * { box-sizing: border-box; margin: 0; padding: 0; }
  html, body {
    width: 1200px;
    height: 750px;
    overflow: hidden;
    background: var(--backdrop);
    font-family: "Source Sans 3", "Myriad Pro", sans-serif;
  }
  .card {
    position: absolute;
    left: 110px;
    top: 95px;
    width: 980px;
    height: 560px;
    background: var(--card-white);
    overflow: hidden;
  }
  .card-panels {
    position: absolute;
    inset: 0;
    width: 980px;
    height: 560px;
  }
  .brand {
    position: absolute;
    left: 570px;
    top: 78px;
    display: flex;
    align-items: center;
    gap: 22px;
  }
  .brand-dot {
    width: 74px;
    height: 74px;
    border-radius: 50%;
    background: var(--accent-yellow);
    flex: none;
  }
  .brand-name {
    font-weight: 600;
    font-size: 46px;
    line-height: 1;
    color: var(--ink);
    text-transform: uppercase;
    letter-spacing: 0.5px;
  }
  .contact-block {
    position: absolute;
    left: 44px;
    top: 290px;
    color: var(--text-light);
  }
  .person-name {
    font-weight: 600;
    font-size: 36px;
    color: var(--accent-yellow);
    margin-bottom: 20px;
    line-height: 1.1;
  }
  .contact-list { list-style: none; }
  .contact-item {
    display: flex;
    align-items: center;
    gap: 12px;
    font-size: 23px;
    line-height: 39px;
  }
  .contact-icon { width: 26px; height: 26px; flex: none; }
  .tagline {
    margin-top: 14px;
    font-style: italic;
    font-weight: 700;
    font-size: 27px;
    color: var(--accent-yellow);
    letter-spacing: 0.3px;
  }
</style>
</head>
<body>
  <section class="card" aria-label="Ridgeline Journeys business card">
    <svg class="card-panels" viewBox="0 0 980 560" aria-hidden="true">
      <defs>
        <linearGradient id="stripe-fill" x1="0" y1="0" x2="0" y2="1">
          <stop offset="0" stop-color="var(--accent-yellow)"/>
          <stop offset="1" stop-color="var(--accent-amber)"/>
        </linearGradient>
      </defs>
      <polygon class="panel-dark" points="0,0 204,0 625,560 0,560" fill="var(--card-black)"/>
      <polygon class="panel-stripe" points="204,0 212,0 674,560 625,560" fill="url(#stripe-fill)"/>
    </svg>

    <div class="brand">
      <span class="brand-dot" aria-hidden="true"></span>
      <span class="brand-name">Ridgeline<br>Journeys</span>
    </div>

    <div class="contact-block">
      <h1 class="person-name">Curtis Halvey</h1>
      <ul class="contact-list">
        <li class="contact-item">
          <svg class="contact-icon" viewBox="0 0 24 24" aria-hidden="true">
            <path fill="var(--accent-yellow)" d="M6.6 10.8c1.4 2.8 3.8 5.1 6.6 6.6l2.2-2.2c.3-.3.7-.4 1-.2 1.1.4 2.3.6 3.6.6.6 0 1 .4 1 1V20c0 .6-.4 1-1 1C10.6 21 3 13.4 3 4c0-.6.4-1 1-1h3.5c.6 0 1 .4 1 1 0 1.3.2 2.5.6 3.6.1.3 0 .7-.2 1z"/>
          </svg>
          <span>612 418 9073</span>
        </li>
        <li class="contact-item">
          <svg class="contact-icon" viewBox="0 0 24 24" aria-hidden="true">
            <rect x="1" y="5" width="22" height="14" fill="var(--accent-yellow)"/>
            <polyline points="1,5 12,13 23,5" fill="none" stroke="var(--card-black)" stroke-width="1.8"/>
          </svg>
          <span>curtis@ridgelinejourneys.com</span>
        </li>
        <li class="contact-item">
          <svg class="contact-icon" viewBox="0 0 24 24" aria-hidden="true">
            <circle cx="12" cy="12" r="11" fill="var(--accent-yellow)"/>
            <ellipse cx="12" cy="12" rx="4.5" ry="11" fill="none" stroke="var(--card-black)" stroke-width="1.6"/>
            <line x1="1" y1="12" x2="23" y2="12" stroke="var(--card-black)" stroke-width="1.6"/>
          </svg>
          <span>www.ridgelinejourneys.com.au</span>
        </li>
      </ul>
      <p class="tagline">Adventure Riding GPS trails</p>
    </div>
  </section>
</body>
</html>
```